creation of a business card design for a company specializing in the creation...

I would like to create a design for a professional business card on a black background and with the company's colors (I am attaching some files: including the logo in horizontal and centered format, I am also attaching a recent project design a T-shirt, this is the one I chose to give you an idea of my preferences.

we are in the process of developing a new website design, it is still in the development phase but it can be viewed at the following address: www.vantrelmo.be to give you other ideas about the company
you will see for yourself the subject of my main activity: company specializing in the construction of stairs

I would like a business card that stands out from the rest with a unique design

here is the informations
Name: Lucien Barthel
Function: Manager
Address: Rue Moulinet du Parc 42
7180 Brenval
telephone: +32 468 219 804
email: info@rx7p.be
website: rx7p. be
social networks: Facebook, YouTube, TikTok, Instagram

Target Market(s)

customer who wants to have a beautiful staircase built

Industry/Entity Type

contruction d'escalier

Contact Information for Business Card

Adresse. Numero de telephone, site web, le texte : "Createur d'escalier", logo recto-verso, icone des reseaux sociaux

Requirements
Must have
• the mention: Stair creator
Nice to have
• an illustration of a designer staircase
Should not have
• do not distort the logo

```html
<!DOCTYPE html>
<html lang="fr">
<head>
<meta charset="utf-8">
<title>Haldor – Business Card</title>
<link href="https://fonts.googleapis.com/css2?family=Ubuntu:wght@400;500;700&display=swap" rel="stylesheet">
<style>
  :root {
    --stage: #2a2a2c;
    --card: #1f1f23;
    --band-light: #6497b6;
    --band-dark: #225468;
    --ink: #ffffff;
    --ink-soft: #d7e4ec;
    --pattern-a: #141416;
    --pattern-b: #3a3a3f;
    --accent: #7fb3d3;
  }
  * { box-sizing: border-box; margin: 0; padding: 0; }
  html, body {
    width: 1200px; height: 780px; overflow: hidden;
    background: var(--stage);
    font-family: "Ubuntu", "Open Sans", sans-serif;
    color: var(--ink);
  }
  .stage {
    position: relative; width: 1200px; height: 780px;
    display: flex; align-items: center; justify-content: center; gap: 40px;
  }
  .card {
    position: relative; width: 540px; height: 310px;
    background: var(--card); overflow: hidden;
    box-shadow: 0 14px 34px rgba(0,0,0,.45);
  }

  /* Front */
  .brand {
    position: absolute; top: 40px; left: 300px;
    display: flex; flex-direction: column; align-items: flex-start; gap: 6px;
  }
  .brand-mark { display: flex; align-items: center; gap: 10px; }
  .brand-dot { width: 18px; height: 18px; border-radius: 50%; background: var(--band-light); }
  .brand-name { font-weight: 500; font-size: 28px; letter-spacing: 2px; color: var(--ink); }
  .brand-tag { font-size: 10px; letter-spacing: 3px; text-transform: uppercase; color: var(--ink-soft); }
  .brand-slogan { font-size: 13px; font-weight: 700; color: var(--ink); letter-spacing: .5px; }

  .band {
    position: absolute; left: 0; right: 0; top: 150px; height: 104px;
    background: linear-gradient(105deg, var(--band-light) 0 52%, var(--band-dark) 52% 100%);
  }
  .person { position: absolute; left: 30px; top: 12px; }
  .person-name { font-weight: 700; font-size: 26px; line-height: 1.1; white-space: nowrap; }
  .person-role { font-size: 16px; margin-top: 6px; padding-left: 70px; }

  .contact {
    position: absolute; left: 306px; top: 14px;
    list-style: none; display: flex; flex-direction: column; gap: 4px;
  }
  .contact li { display: flex; align-items: center; gap: 9px; font-size: 17px; white-space: nowrap; }
  .contact svg { width: 14px; height: 14px; flex: none; }

  .address { position: absolute; left: 30px; top: 268px; font-size: 16px; color: var(--ink); white-space: nowrap; }

  /* Back */
  .pattern {
    position: absolute; inset: 0;
    background: linear-gradient(120deg, var(--pattern-a) 0%, var(--pattern-a) 45%, var(--pattern-b) 78%, #6a6a70 100%);
  }
  .back-brand {
    position: absolute; left: 40px; bottom: 34px;
    display: flex; flex-direction: column; gap: 4px;
  }
  .back-brand .brand-square { width: 16px; height: 16px; background: var(--accent); }
  .back-brand .brand-name { font-size: 24px; }
</style>
</head>
<body>
<main class="stage">

  <section class="card card-front" aria-label="Recto">
    <div class="brand">
      <div class="brand-mark">
        <span class="brand-dot"></span>
        <span class="brand-name">Haldor</span>
      </div>
      <span class="brand-tag">Crafted stairways</span>
      <span class="brand-slogan">Bâtisseur de marches</span>
    </div>

    <div class="band">
      <div class="person">
        <p class="person-name">Lucien Barthel</p>
        <p class="person-role">Manager</p>
      </div>
      <ul class="contact">
        <li>
          <svg viewBox="0 0 16 16" aria-hidden="true"><path fill="#fff" d="M3.5 1.5l2.4 2.4-1.4 2a9 9 0 0 0 5.6 5.6l2-1.4 2.4 2.4-1.6 2C7 14 2 9 1.5 3.1z"/></svg>
          <span>+32 468 219 804</span>
        </li>
        <li>
          <svg viewBox="0 0 16 16" aria-hidden="true"><rect x="1" y="3" width="14" height="10" rx="1" fill="none" stroke="#fff" stroke-width="1.6"/><path d="M1.5 4l6.5 5 6.5-5" fill="none" stroke="#fff" stroke-width="1.6"/></svg>
          <span>info@rx7p.be</span>
        </li>
        <li>
          <svg viewBox="0 0 16 16" aria-hidden="true"><circle cx="8" cy="8" r="6.6" fill="none" stroke="#fff" stroke-width="1.4"/><ellipse cx="8" cy="8" rx="3" ry="6.6" fill="none" stroke="#fff" stroke-width="1.2"/><path d="M1.5 8h13" stroke="#fff" stroke-width="1.2"/></svg>
          <span>www.rx7p.be</span>
        </li>
      </ul>
    </div>

    <p class="address">Rue Moulinet du Parc 42 7180 Brenval</p>
  </section>

  <section class="card card-back" aria-label="Verso">
    <div class="pattern" role="img" aria-label="Motif répété de la marque sur fond noir, reflet argenté"></div>
    <div class="back-brand">
      <div class="brand-mark">
        <span class="brand-square"></span>
        <span class="brand-name">Haldor</span>
      </div>
      <span class="brand-tag">Crafted stairways</span>
    </div>
  </section>

</main>
</body>
</html>
```